website design for M&T Electric

A portfolio website for a high end commercial and residential electrical contracting company. The current site mandtelectric.example does not represent the current direction but the images in the gallery give you an idea of the work we do. Current logo will be uploaded shortly but is black text on white background.
Target Market(s)
General Contractors, Residential Home Owners, clients intersted in Velmora home automation.
Industry/Entity Type
Electrician
Coding
Coded - Design and coding required
Number of Pages Required
2 page
Font styles to use
Sans Serif
Colors
Designer to choose colors to be used in the design.
Requirements
Must have
- Portfolio section highlighting different service areas and products (Velmora Housepilot, etc)

```html
<!DOCTYPE html>
<html lang="en">
<head>
<meta charset="utf-8">
<title>M&amp;T Electric</title>
<link rel="stylesheet" href="https://fonts.googleapis.com/css2?family=Cormorant+Garamond:wght@400;500;700&family=Roboto:wght@300;400;500&display=swap">
<style>
:root{
  --ink:#111;
  --bar:#1b1b1b;
  --white:#fff;
  --muted:#8c8c8c;
  --text:#555;
  --line:#d6d6d6;
  --btn:#0d0d0d;
  --footer:#050505;
}
*{margin:0;padding:0;box-sizing:border-box}
html,body{width:1200px;height:3077px;overflow:hidden;background:var(--white)}
body{position:relative;font-family:"Roboto",Arial,sans-serif;color:var(--ink)}
.abs{position:absolute}
.serif{font-family:"Cormorant Garamond",Georgia,serif}

/* top bar */
.topbar{left:0;top:0;width:1200px;height:45px;background:var(--bar);color:var(--white);font-size:19px}
.topbar .phone{left:76px;top:10px;display:flex;gap:12px;align-items:center}
.topbar .divider{left:272px;top:10px;width:2px;height:26px;background:#888}
.topbar .mail{left:302px;top:13px;font-size:14px;display:flex;gap:10px;align-items:center}
.topbar .socials{left:786px;top:15px;display:flex;gap:24px}
.topbar .socials span{width:14px;height:14px;border:2px solid #e6e6e6;display:block}
.topbar .search{left:944px;top:8px;width:178px;height:30px;border-left:1px solid #666;padding-left:12px;font-size:12px;color:#aaa;line-height:30px}
.topbar .search svg{position:absolute;right:0;top:6px}

/* header */
.header{left:0;top:45px;width:1200px;height:95px;background:var(--white);border-bottom:1px solid #eee}
.logo{left:84px;top:18px;font-size:50px;font-weight:700;letter-spacing:1px}
.nav{left:548px;top:32px;display:flex;gap:40px;font-size:16px;color:var(--muted)}
.nav a{color:inherit;text-decoration:none;padding-bottom:20px}
.nav a.active{color:var(--ink);border-bottom:3px solid var(--ink)}

/* hero */
.hero{left:0;top:140px;width:1200px;height:572px;
  background:
    radial-gradient(ellipse 260px 120px at 870px 330px,rgba(230,170,90,.55),transparent 70%),
    radial-gradient(ellipse 220px 110px at 330px 300px,rgba(220,160,80,.45),transparent 70%),
    radial-gradient(ellipse 500px 200px at 600px 260px,rgba(150,120,90,.35),transparent 70%),
    linear-gradient(180deg,#1c2636 0%,#2e3b4b 28%,#4a4639 50%,#26301f 72%,#3a3c38 86%,#1a1c18 100%)}
.hero::after{content:"";position:absolute;inset:0;background:radial-gradient(ellipse at center,transparent 50%,rgba(0,0,0,.35) 100%)}
.hero > *{z-index:1}
.hero-title{left:0;top:135px;width:1200px;text-align:center;color:var(--white);font-size:66px;font-weight:500}
.hero-rule{left:472px;top:225px;width:296px;height:2px;background:var(--white)}
.hero-quote{left:0;top:248px;width:1200px;text-align:center;color:var(--white);font-size:30px}
.hero-quote b{font-size:46px;font-weight:700}
.hero-sub{left:0;top:306px;width:1200px;text-align:center;color:var(--white);font-size:19px}
.zip{left:420px;top:344px;width:196px;height:62px;border:2px solid var(--white);background:rgba(0,0,0,.25);color:var(--white);font-size:19px;padding:18px 14px}
.find{left:622px;top:344px;width:156px;height:62px;background:var(--white);font-size:22px;text-align:center;line-height:62px}
.arrow{top:221px;width:62px;height:58px;background:var(--white);font-size:36px;text-align:center;line-height:54px}

/* about */
.section-title{font-size:44px;text-align:center;font-weight:500}
.about-title{left:0;top:762px;width:1200px}
.about-text{left:150px;top:832px;width:900px;text-align:center;font-size:14.5px;line-height:24px;color:var(--text)}
.btn{background:var(--btn);color:var(--white);text-align:center;font-size:21px}
.about-btn{left:515px;top:921px;width:170px;height:51px;line-height:51px}

/* gallery */
.ph{position:absolute}
.gallery-title{left:740px;top:1082px;width:280px;font-size:44px;text-align:center;font-weight:500}

/* services */
.services{left:0;top:1969px;width:1200px;height:416px;
  background:
    radial-gradient(ellipse 300px 200px at 150px 120px,rgba(120,80,45,.5),transparent 70%),
    radial-gradient(ellipse 300px 200px at 1080px 140px,rgba(110,75,45,.5),transparent 70%),
    linear-gradient(180deg,#241812 0%,#3e2a1c 45%,#2b1d14 100%)}
.card{top:144px;width:332px;height:207px;background:var(--white);text-align:center}
.card h3{position:absolute;left:0;top:90px;width:100%;font-family:"Roboto",Arial,sans-serif;font-weight:400;font-size:21px}
.card p{position:absolute;left:20px;top:128px;width:292px;font-size:14px;line-height:21px;color:var(--text)}
.card .btn{position:absolute;left:82px;top:188px;width:170px;height:50px;line-height:50px;border:1px solid #777}
.disc{top:48px;width:174px;height:174px;border-radius:50%;border:7px solid var(--white)}

/* product */
.product-title{left:190px;top:2432px;width:296px}
.categories{left:76px;top:2502px;width:322px;height:312px;border:1px solid var(--line)}
.categories h4{position:absolute;left:36px;top:-12px;background:var(--white);padding:0 4px;font-size:19px;font-weight:500}
.cat{position:absolute;left:36px;font-family:"Cormorant Garamond",Georgia,serif;font-size:14.5px;color:#333;font-weight:500}
.cat.u{text-decoration:underline}
.product-text{left:420px;top:2540px;width:244px;font-size:16px;line-height:27px;color:#333}
.product-btn{left:437px;top:2698px;width:170px;height:51px;line-height:51px}
.frame{left:675px;top:2439px;width:447px;height:309px;border:1px solid var(--line);padding:10px}
.dots{left:868px;top:2758px;display:flex;gap:6px;align-items:center}
.dots span{width:10px;height:10px;border-radius:50%;border:1px solid #333}
.dots span.on{width:16px;height:16px;border-width:3px}

/* footer */
.footer{left:0;top:2867px;width:1200px;height:210px;background:var(--footer);color:var(--white)}
.fnav{left:80px;top:30px;display:flex;gap:22px;font-size:14px}
.fsocial{left:930px;top:30px;display:flex;gap:34px}
.fsocial span{width:18px;height:18px;border:2px solid #ddd;display:block}
.frule{left:80px;top:66px;width:1040px;height:1px;background:#444}
.fblock{top:104px;font-size:13.5px;line-height:21px;display:flex;gap:16px}
.copy{left:940px;top:124px;width:182px;text-align:right;font-size:14px;line-height:21px}
.copy b{font-family:"Cormorant Garamond",Georgia,serif;font-size:19px}
</style>
</head>
<body>

<div class="abs topbar">
  <div class="abs phone">
    <svg width="18" height="18" viewBox="0 0 24 24"><path fill="#fff" d="M6.6 10.8a15 15 0 0 0 6.6 6.6l2.2-2.2a1 1 0 0 1 1-.25 11.4 11.4 0 0 0 3.6.6 1 1 0 0 1 1 1V20a1 1 0 0 1-1 1A17 17 0 0 1 3 4a1 1 0 0 1 1-1h3.5a1 1 0 0 1 1 1c0 1.25.2 2.45.6 3.6a1 1 0 0 1-.25 1z"/></svg>
    (555) 014-2290
  </div>
  <div class="abs divider"></div>
  <div class="abs mail">
    <svg width="18" height="13" viewBox="0 0 18 13"><rect x="0.5" y="0.5" width="17" height="12" fill="#fff"/><path d="M1 1l8 6 8-6" stroke="#1b1b1b" fill="none"/></svg>
    jmarlow@mandtelectric.example
  </div>
  <div class="abs socials" aria-label="Social links"><span></span><span></span><span></span><span></span></div>
  <div class="abs search">Search
    <svg width="18" height="18" viewBox="0 0 18 18"><circle cx="7" cy="7" r="5.5" stroke="#fff" stroke-width="2" fill="none"/><path d="M11 11l6 6" stroke="#fff" stroke-width="2.5"/></svg>
  </div>
</div>

<header class="abs header">
  <div class="abs logo serif">M&amp;T Electric</div>
  <nav class="abs nav">
    <a class="active">HOME</a><a>ABOUT US</a><a>SERVICES</a><a>GALLERY</a><a>CONTACT US</a>
  </nav>
</header>

<section class="abs hero" role="img" aria-label="Large home lit at dusk">
  <div class="abs hero-title serif">M &amp; T Electric</div>
  <div class="abs hero-rule"></div>
  <div class="abs hero-quote serif">Get Multiple <b>FREE</b> Electrical Quotes.</div>
  <div class="abs hero-sub">Where do you need the electrical contractor?</div>
  <div class="abs zip">Zip Code</div>
  <div class="abs find">FIND PROS</div>
  <div class="abs arrow" style="left:0">&laquo;</div>
  <div class="abs arrow" style="left:1138px">&raquo;</div>
</section>

<section>
  <h2 class="abs section-title about-title serif">About Us</h2>
  <p class="abs about-text">M &amp; T Electric is a full service electrical contracting shop. We offer commercial, residential, light industrial, and agricultural services. We're Velmora Housepilot and Velmora Motorized Shades certified, as well as an authorized Voltarra generator dealer. We've served the Silver Creek and Central Valley area for over 18 years.</p>
  <div class="abs btn about-btn">READ MORE</div>
</section>

<section>
  <div class="ph" style="left:172px;top:1023px;width:271px;height:230px;background:radial-gradient(ellipse 90px 60px at 50% 25%,rgba(240,190,110,.7),transparent 70%),linear-gradient(160deg,#7a4526,#4a2814 55%,#1e120a)" role="img" aria-label="Wood panelled dining room with chandelier"></div>
  <div class="ph" style="left:453px;top:1023px;width:271px;height:230px;background:radial-gradient(ellipse 120px 50px at 50% 15%,rgba(255,200,120,.75),transparent 70%),linear-gradient(170deg,#b07a42,#6a4022 55%,#3a2414)" role="img" aria-label="Living room with warm ceiling lighting"></div>
  <h2 class="abs gallery-title serif">Our Gallery</h2>
  <div class="ph" style="left:172px;top:1263px;width:552px;height:415px;background:linear-gradient(180deg,#b5bac0 0%,#c6c8c6 30%,#b8ad98 48%,#8e8572 62%,#6d6a64 78%,#857a70 100%)" role="img" aria-label="Company office building exterior"></div>
  <div class="ph" style="left:736px;top:1210px;width:292px;height:468px;background:radial-gradient(ellipse 110px 150px at 50% 35%,rgba(245,230,200,.9),transparent 75%),linear-gradient(180deg,#6e5a45,#a89478 45%,#5c4c3a)" role="img" aria-label="Stone wall fountain with sconces"></div>
  <div class="ph" style="left:172px;top:1692px;width:277px;height:228px;background:radial-gradient(ellipse 120px 80px at 55% 55%,#f4f3ff,transparent 75%),linear-gradient(135deg,#6d62e0,#b9b5f5 50%,#5a4fd0)" role="img" aria-label="Modern reception with blue accent lighting"></div>
  <div class="ph" style="left:463px;top:1692px;width:275px;height:228px;background:linear-gradient(180deg,#e4e2dc 0%,#cfcbc2 45%,#8b8a88 60%,#6f6e6c 100%)" role="img" aria-label="Gallery room with grey plank floor"></div>
  <div class="ph" style="left:751px;top:1692px;width:277px;height:228px;background:radial-gradient(ellipse 90px 60px at 70% 40%,rgba(240,235,225,.8),transparent 70%),linear-gradient(180deg,#4a3020,#8a6a50 45%,#3c2a1e)" role="img" aria-label="Open dining hall with pendant lights"></div>
</section>

<section class="abs services" role="img" aria-label="Library interior with bookshelves">
  <div class="abs card" style="left:78px"><h3>Residential</h3><p>Lorem Ipsum is simply dummy text of the printing and typesetting industry</p><div class="btn">READ MORE</div></div>
  <div class="abs card" style="left:433px"><h3 style="color:#555">Commercial</h3><p>Lorem Ipsum is simply dummy text of the printing and typesetting industry</p><div class="btn">READ MORE</div></div>
  <div class="abs card" style="left:788px"><h3>Light industrial</h3><p>Lorem Ipsum is simply dummy text of the printing and typesetting industry</p><div class="btn">READ MORE</div></div>
  <div class="abs disc" style="left:157px;background:radial-gradient(circle at 50% 40%,#d09a5a,#6a3e20 60%,#3a2212)" role="img" aria-label="Residential great room"></div>
  <div class="abs disc" style="left:512px;background:linear-gradient(180deg,#7fa4d4 0%,#a08870 40%,#7a5a44 65%,#5a5a5a 100%)" role="img" aria-label="Commercial stone building"></div>
  <div class="abs disc" style="left:868px;background:radial-gradient(circle at 50% 60%,#c27a40,#5a2e18 60%,#2a160c)" role="img" aria-label="Industrial pendant bulbs"></div>
</section>

<section>
  <h2 class="abs section-title product-title serif">Our Product</h2>
  <div class="abs categories">
    <h4>CATEGORIES</h4>
    <div class="cat u" style="top:58px">Velmora Housepilot Certified</div>
    <div class="cat u" style="top:82px;left:168px">Features</div>
    <div class="cat" style="top:104px;left:168px">Information</div>
    <div class="cat" style="top:154px;line-height:19px">Velmora Shadeline Motorized<br>Shades Certified</div>
    <div class="cat" style="top:216px">LED Lighting</div>
    <div class="cat" style="top:258px">Emergency Generators</div>
  </div>
  <p class="abs product-text">We're proudly certified to install Velmora Housepilot systems. Housepilot gives you complete control over your home lighting with just a few simple buttons.</p>
  <div class="abs btn product-btn">READ MORE</div>
  <div class="abs frame"><div style="width:100%;height:100%;background:radial-gradient(ellipse 120px 110px at 50% 45%,#4a4a48,#6a665e 60%,transparent 72%),linear-gradient(135deg,#efe4d2,#d8c8ae)" role="img" aria-label="Wall-mounted lighting keypad panels"></div></div>
  <div class="abs dots"><span></span><span class="on"></span><span></span></div>
</section>

<footer class="abs footer">
  <div class="abs fnav"><span>Home</span><span>Services</span><span>Products</span><span>Gallery</span><span>Contact Us</span></div>
  <div class="abs fsocial" aria-label="Social links"><span></span><span></span><span></span><span></span></div>
  <div class="abs frule"></div>
  <div class="abs fblock" style="left:78px">
    <svg width="24" height="26" viewBox="0 0 24 26"><path d="M11 0h2v26h-2z M2 4h18l4 3-4 3H2z M4 13h18v6H4l-4-3z" fill="#fff"/></svg>
    <div>POSTAL ADDRESS<br>220 Hangar Lane<br>PO Box 4120 , Pinecrest, ID 83000</div>
  </div>
  <div class="abs fblock" style="left:348px">
    <svg width="24" height="24" viewBox="0 0 24 24"><path fill="none" stroke="#fff" stroke-width="1.5" d="M6.6 10.8a15 15 0 0 0 6.6 6.6l2.2-2.2a1 1 0 0 1 1-.25 11.4 11.4 0 0 0 3.6.6 1 1 0 0 1 1 1V20a1 1 0 0 1-1 1A17 17 0 0 1 3 4a1 1 0 0 1 1-1h3.5a1 1 0 0 1 1 1c0 1.25.2 2.45.6 3.6a1 1 0 0 1-.25 1z"/></svg>
    <div>PHONE<br>(555) 014-2290</div>
  </div>
  <div class="abs fblock" style="left:568px">
    <svg width="26" height="20" viewBox="0 0 26 20"><rect x="1" y="1" width="24" height="18" fill="none" stroke="#fff" stroke-width="1.5"/><path d="M1 1l12 9 12-9" fill="none" stroke="#fff" stroke-width="1.5"/></svg>
    <div>EMAIL<br>kreyes@mandtelectric.example<br>jmarlow@mandtelectric.example</div>
  </div>
  <div class="abs copy">&copy; <b>M&amp;T Electric</b><br>- 2017 All Right Reserved</div>
</footer>

</body>
</html>
```